Design letter head and business card

Hello,

you should design a business card and letter paper for Kranichflug Marketing. In German we write this word with K insteat of C.

Company does not have a logo. But in general, we write Kranichflug Marketing in 2 lines.
First line red: KRANICHFLUG
Second line gray: MARKETING

Red (or wine red) and Gray / Black are our favorite colors.

Company slogan: "Fresh Ground Online Marketing".

Company offers SEO, SEM, SEA, AdWords, Conversion Optimization, Online Markting Consulting ...

The website is old, please do not use this as base for your task.

German letter paper sizes:
Viawable Dimensions : 210 x 297 mm
Needed file dimensions: 212 x 299 mm

Informations to include:

Address:
Kranichflug Marketing GmbH
Lindenweg 23
71592 Weinstadt
Germany

Geschäftsführer | CEO: Bernhard Olzner

Phone: +49 (0) 4821 846 27 05

Fax: +49 (0) 4821 846 27 88

Mail: info@kranichflug-beispiel.de

Web: www.kranichflug-beispiel.de

Amtsgericht Lindenau, HRB 537264

Bank: Rosenauer Bank
IBAN: DE827315480900XXXXXXXX
BIC: GENODES1RSQ

Thanks

Bernhard

Target Market(s)

People who likes to win the online marketing game.

Industry/Entity Type

Business

Contact Information for Business Card

Here is the personal text on the card:

Name:
Bernhard Olzner

Title:
Geschäftsführer | CEO

Address:
Kranichflug Marketing GmbH
Lindenweg 23
71592 Weinstadt
Germany

Phone:
+49 (0) 4821 846 27 05

Fax:
+49 (0) 4821 846 27 88

Mail:
olzner@kranichflug-beispiel.de

Web:
www.kranichflug-beispiel.de

Business Card:
Viewable Dimensions: 85 x 55 mm
Needed file dimensions: 87 x 57mm

Font styles to use
Sans Serif

Requirements
Nice to have
• It would be great to see the dynamics of a helicopter.

```html
<!DOCTYPE html>
<html lang="de">
<head>
<meta charset="utf-8">
<title>Kranichflug Marketing – Briefpapier</title>
<link rel="stylesheet" href="https://fonts.googleapis.com/css2?family=Encode+Sans+Condensed:wght@400;700&family=Encode+Sans+Semi+Condensed:wght@400&display=swap">
<style>
  :root {
    --wine: #8e1f25;
    --sidebar: #e6e6e8;
    --paper: #ffffff;
    --frame: #c9c9c9;
    --ink: #2b2b2b;
    --display-font: "Encode Sans Condensed", "Arial Narrow", sans-serif;
    --text-font: "Encode Sans Semi Condensed", "Arial Narrow", sans-serif;
  }
  html, body {
    margin: 0;
    padding: 0;
    width: 851px;
    height: 1200px;
    overflow: hidden;
    background: var(--paper);
  }
  .letterhead {
    position: relative;
    width: 849px;
    height: 1198px;
    border: 1px solid var(--frame);
    background: var(--paper);
    font-family: var(--text-font);
    color: var(--ink);
  }
  .sidebar {
    position: absolute;
    left: 0;
    top: 0;
    width: 237px;
    height: 100%;
    background: var(--sidebar);
  }
  .sidebar-band {
    position: absolute;
    left: 0;
    width: 100%;
    background: var(--wine);
  }
  .sidebar-band--top { top: 0; height: 28px; }
  .sidebar-band--bottom { bottom: 0; height: 24px; }

  .brand {
    position: absolute;
    left: 38px;
    top: 148px;
    width: 180px;
  }
  .brand-mark {
    display: block;
    width: 14px;
    height: 14px;
    background: var(--wine);
    margin: 0 0 10px 2px;
  }
  .brand-name {
    margin: 0;
    font-family: var(--display-font);
    font-weight: 700;
    font-size: 30px;
    line-height: 28px;
    letter-spacing: 0.2px;
    color: var(--wine);
    text-transform: uppercase;
    white-space: nowrap;
  }
  .brand-slogan {
    margin: 9px 0 0;
    font-family: var(--display-font);
    font-weight: 400;
    font-size: 14.5px;
    color: var(--ink);
    white-space: nowrap;
  }

  .company-details {
    position: absolute;
    left: 23px;
    top: 942px;
    width: 212px;
    font-size: 13px;
    line-height: 18px;
    white-space: nowrap;
  }
  .company-details p {
    margin: 0 0 9px;
  }
</style>
</head>
<body>
  <main class="letterhead">
    <aside class="sidebar">
      <div class="sidebar-band sidebar-band--top"></div>

      <header class="brand">
        <span class="brand-mark"></span>
        <h1 class="brand-name">Kranichflug<br>Marketing</h1>
        <p class="brand-slogan">Fresh Ground Online Marketing</p>
      </header>

      <section class="company-details">
        <p class="company-address">
          Kranichflug Marketing GmbH,<br>
          Lindenweg 23<br>
          71592 Lindenau, Germany
        </p>
        <p class="company-contact">
          Phone: +49 (0) 4821 846 27 05;<br>
          Fax: +49 (0) 4821 846 27 88<br>
          E-mail: info@kranichflug-beispiel.de<br>
          web: www.kranichflug-beispiel.de
        </p>
        <p class="company-register">
          Amtsgericht Lindenau, HRB 537264<br>
          Bank: Rosenauer Bank<br>
          IBAN: DE827315480900XXXXXXXX<br>
          BIC: GENODES1RSQ
        </p>
      </section>

      <div class="sidebar-band sidebar-band--bottom"></div>
    </aside>
  </main>
</body>
</html>
```